Food Processing Economic Development Postcard

Tarrow Basin Economic Development Council (TBEDC) is one of the leading economic development agencies in New Mexico. We serve all communities of Doña Ana County’s 3,815 sq. miles of land, located in southern New Mexico, adjacent to El Paso and Mexico. The purpose of this postcard is to recruit potential food processing companies located in California to explore the potential expanding to Doña Ana County. We are looking for a two-sided, color oversize postcard (8.52” x 5.47”) with address section to help promote our region.

Our initial design concept for the front would be a child riding a roller coaster afraid with a main message stating something along the lines of “Having trouble stomaching the California Business Climate?” and a second line saying “Shouldn’t doing business be more enchanting….” Our company logo would also need to be placed in the front somewhere.

The back of the postcard would show some sort of excited/happy child about food with the main message being “Let us show you a better place!” Our company contact information should be placed somewhere on the back

Alternatively imagery could show a sad or crying child standing in the rain or other bad weather. Message could include “tired of the business climate in California?” Second image on reverse side could show child playing in the sun with the same tagline “Shouldn’t doing business be more enchanting”.

These are ideas and we encourage the creativity of the design community in suggestions on getting this message through.

The following information would need to be added on the back postcard.
Holcombe & Reyes recently ranked New Mexico “Best in the West for Manufacturing” Doña Ana County has the following to offer your company.

Doña Ana County is home to 2,184 (UP 24% from 2007) farms with over 659,000 acres of farmland (Up 12% since 2007). We are one of the top producers in the U.S. for pecans and chile, the second largest vegetable producer in NM, and home to one of the top five largest dairies in the country.

Location (bulleted list)
• Equidistant between ports of Long Beach and Houston
• 2 Interstates (I-10, I-25)
• 2 railroads (KQRT, Silverline Freight)
• Port of Entry with Mexico and a Border Overweight Zone
• 340 Days of Sunshine, low humidity, and rare inclement weather

Potential Incentives (bulleted list)
• Job Closing Fund
• On the Job Training
• Land Trade for Job Creation
• Property Tax Abatements and low property assessments

Companies that know Already (bulleted list)
• Brisk Foods
• Whitlock Enterprises
• Torvo Chile
• El Roble Winery
• Pulvatech
• Merrit Harvest Foods
• Summit Chill Storage
• R&K Dairy
• Red Mesa Almonds

We are very open to other artistic ideas to get our message across beyond visual concepts of roller coaster rides as long as it depicts or translates the message of a better opportunity and business climate in Doña Ana County than their current location. The facts on the back must stay the same but the main tagline message on front and back can be replaced to better fit the images chosen for the postcard. Also note that the tagline originally proposed plays on New Mexico’s nickname “Land of Enchantment.” Special symbolism that illustrates creative messaging that can incorporate local community or statewide meanings in favor of New Mexico will be given preference, but this is not a requirement.

Company contact info.
TBEDC
800-417-2950
tarrowregion-example.com/Food

Also attached is the company logo (TBEDC) to be used in the design and a couple images to give an idea of where we are located. These images may be used in your design to highlight our location or you may choose to use something different. We have also attached a secondary right space logo which we occasionally use on some of our publications with you may choose to use in your designs.

```html
<!DOCTYPE html>
<html lang="en">
<head>
<meta charset="utf-8">
<title>TBEDC Food Processing Postcard</title>
<link href="https://fonts.googleapis.com/css2?family=Open+Sans:ital,wght@0,400;0,600;0,700;0,800;1,700;1,800&display=swap" rel="stylesheet">
<style>
:root{
  --navy:#1d3a6e;
  --blue:#2a5aa8;
  --orange:#f39a1e;
  --yellow:#f6c343;
  --cream:#fdf8ee;
  --ink:#2b2b2b;
  --grey:#8a8f96;
  --bg:#e9e6e1;
  --white:#ffffff;
}
*{box-sizing:border-box;margin:0;padding:0}
html,body{width:816px;height:1200px;overflow:hidden;background:var(--bg);font-family:"Open Sans",Arial,sans-serif;color:var(--ink)}
.card{position:absolute;left:36px;width:744px;height:478px;background:var(--white);overflow:hidden;box-shadow:0 3px 10px rgba(0,0,0,.25)}
.card--front{top:60px}
.card--back{top:632px;background:var(--cream)}

/* front */
.front-photo{position:absolute;inset:0;background:linear-gradient(180deg,#9aa3ab 0%,#b8bec3 45%,#8f9d76 72%,#5f7a3c 100%)}
.return-address{position:absolute;left:22px;top:20px;font-size:11px;line-height:1.35;color:var(--ink);background:rgba(255,255,255,.7);padding:4px 8px}
.front-band{position:absolute;left:0;right:0;bottom:0;height:74px;background:var(--white);border-top:5px solid var(--orange);display:flex;align-items:center;justify-content:space-between;padding:0 26px}
.front-tagline{font-size:25px;font-weight:800;font-style:italic;color:var(--navy)}
.brand{display:flex;align-items:center;gap:8px;font-size:26px;font-weight:800;color:var(--navy)}
.brand-square{width:18px;height:18px;background:var(--orange)}

/* back */
.back-left{position:absolute;left:0;top:0;width:440px;height:100%}
.headline{position:absolute;left:150px;top:18px;width:280px;font-size:17px;font-weight:800;color:var(--navy);line-height:1.2}
.intro{position:absolute;left:150px;top:68px;width:280px;font-size:9.5px;line-height:1.4}
.intro p{margin-bottom:6px}
.intro strong{color:var(--navy)}
.child-photo{position:absolute;left:18px;top:22px;width:122px;height:122px;border-radius:50%;border:4px solid var(--white);background:radial-gradient(circle at 50% 35%,#bfe3f7,#7fc3ea 55%,#6db04a 80%);box-shadow:0 2px 5px rgba(0,0,0,.25)}
.map{position:absolute;left:250px;top:218px;width:180px;height:140px;background:linear-gradient(135deg,#f3e2b8,#e6c889);border:1px solid #d0b170}
.facts{position:absolute;left:18px;top:218px;width:225px;font-size:9.5px;line-height:1.38}
.facts h3{font-size:11px;font-weight:800;color:var(--navy);margin-bottom:2px}
.facts ul{list-style:none}
.facts li::before{content:"• ";color:var(--orange);font-weight:700}
.wave{position:absolute;left:0;bottom:0;width:440px;height:100px}
.incentives{position:absolute;left:18px;bottom:10px;width:400px;font-size:9.5px;line-height:1.38;color:var(--white)}
.incentives h3{font-size:11px;font-weight:800;margin-bottom:2px}
.incentives ul{list-style:none}
.incentives li::before{content:"• "}
.divider{position:absolute;left:452px;top:24px;bottom:24px;width:1px;background:var(--grey)}
.back-right{position:absolute;left:466px;top:0;width:262px;height:100%}
.badge{position:absolute;right:0;top:20px;display:flex;align-items:center;gap:8px;font-size:15px;font-weight:800;color:var(--blue)}
.badge-square{width:34px;height:34px;background:var(--yellow)}
.contact{position:absolute;left:0;top:74px;font-size:11px;line-height:1.5}
.contact-row{display:flex;align-items:center;gap:6px;font-weight:700;color:var(--navy)}
.contact-row--phone{font-size:14px}
.contact-note{margin-top:4px;font-size:10px;color:var(--ink);width:220px}
.address-lines{position:absolute;left:0;top:172px;width:250px}
.address-lines span{display:block;height:22px;border-bottom:1px solid var(--grey)}
.companies{position:absolute;left:40px;right:0;top:274px;height:184px;background:var(--white);border:2px solid var(--orange);padding:8px 12px;font-size:10px;line-height:1.42}
.companies h3{font-size:11px;font-weight:800;color:var(--navy);margin-bottom:3px}
.companies ul{list-style:none}
.companies li::before{content:"• ";color:var(--orange);font-weight:700}
</style>
</head>
<body>

<section class="card card--front">
  <div class="front-photo" role="img" aria-label="Child holding an umbrella in the rain on a grassy field with a grey city skyline behind"></div>
  <div class="return-address">Return to:<br>P.O. Box 4471 Tarrow, NM 88210-4471</div>
  <div class="front-band">
    <p class="front-tagline">Tired of the business climate in California?</p>
    <div class="brand"><span class="brand-square"></span>TBEDC</div>
  </div>
</section>

<section class="card card--back">
  <div class="back-left">
    <div class="child-photo" role="img" aria-label="Child playing in the sunshine on green grass"></div>
    <h2 class="headline">Shouldn't doing business be more ENCHANTING?</h2>
    <div class="intro">
      <p><strong>Las Cruces MSA and Doña Ana County welcomes your company.</strong></p>
      <p>Holcombe &amp; Reyes recently ranked New Mexico <strong>“Best in the West for Manufacturing”</strong> and Doña Ana County is home to 2,184 farms (UP 24% from 2007).</p>
      <p>With over 659,000 acres of farmland <strong>(Up 12% since 2007)</strong>, we are one of the <strong>top producers</strong> in the U.S. for pecans and chile, 2nd largest vegetable producer in NM, and home to one of the top five largest dairies in the country.</p>
    </div>
    <div class="map" role="img" aria-label="Regional map of southern New Mexico, El Paso and the Mexico border"></div>
    <div class="facts">
      <h3>Location</h3>
      <ul>
        <li>Equidistant between Ports of Long Beach and Houston</li>
        <li>2 Interstates (I-10, I-25)</li>
        <li>2 railroads (KQRT, Silverline Freight)</li>
        <li>Port of Entry with Mexico and a Border Overweight Zone</li>
        <li>340 days of sunshine, low humidity, and rare inclement weather</li>
      </ul>
    </div>
    <svg class="wave" viewBox="0 0 440 100" preserveAspectRatio="none" aria-hidden="true">
      <path d="M0 18 C120 0 260 30 440 10 L440 100 L0 100 Z" fill="var(--orange)"/>
    </svg>
    <div class="incentives">
      <h3>Potential Incentives</h3>
      <ul>
        <li>Job Closing Fund · On the Job Training</li>
        <li>Land Trade for Job Creation</li>
        <li>Property Tax Abatements and Low Property Assessments</li>
      </ul>
    </div>
  </div>

  <div class="divider"></div>

  <div class="back-right">
    <div class="badge"><span class="badge-square"></span>Open Range Sites</div>
    <div class="contact">
      <div class="contact-row contact-row--phone">
        <svg width="14" height="14" viewBox="0 0 24 24" aria-hidden="true"><path fill="var(--navy)" d="M6.6 10.8a15 15 0 0 0 6.6 6.6l2.2-2.2c.3-.3.7-.4 1-.2 1.1.4 2.3.6 3.6.6.6 0 1 .4 1 1V20c0 .6-.4 1-1 1A17 17 0 0 1 3 4c0-.6.4-1 1-1h3.5c.6 0 1 .4 1 1 0 1.3.2 2.5.6 3.6.1.3 0 .7-.2 1z"/></svg>
        800-417-2950
      </div>
      <div class="contact-row">
        <svg width="14" height="14" viewBox="0 0 24 24" aria-hidden="true"><circle cx="12" cy="12" r="9" fill="none" stroke="var(--navy)" stroke-width="2"/><path d="M3 12h18M12 3c3 3 3 15 0 18M12 3c-3 3-3 15 0 18" fill="none" stroke="var(--navy)" stroke-width="1.5"/></svg>
        tarrowregion-example.com/Food
      </div>
      <p class="contact-note">Contact us to plant your business in Southern New Mexico.</p>
    </div>
    <div class="address-lines"><span></span><span></span><span></span><span></span></div>
    <div class="companies">
      <h3>Companies that know already:</h3>
      <ul>
        <li>Brisk Foods</li>
        <li>Whitlock Enterprises</li>
        <li>Torvo Chile</li>
        <li>El Roble Winery</li>
        <li>Pulvatech</li>
        <li>Merrit Harvest Foods</li>
        <li>Summit Chill Storage</li>
        <li>R&amp;K Dairy</li>
        <li>Red Mesa Almonds</li>
      </ul>
    </div>
  </div>
</section>

</body>
</html>
```